CAMBRAI CELEBRATES ANDOUILETTE

On the occasion of the big annual sale, in CAMBRAI, the 57th celebrates the Cambrai specialty "andouillette de CAMBRAI".

On this occasion, we are developing a special menu for this day;

- Authentic CAMBRAI sausage, old-fashioned mustard sauce, served with fresh fries cooked in beef fat and green salad
- CAMBRAI andouillette salad (lettuce, tomatoes, onions, CAMBRAI andouillette, Tome de CAMBRAI, Cambrai apples
- Andouillette gratin (Homemade mash, CAMBRAI andouillette, old-fashioned mustard, gratin with CAMBRAI tome
- BRUSCHETTA: Cream base, CAMBRAI sausage, CAMBRAI tome, onions, old-fashioned mustard
- Grilled ham
- Fried mussels, with CAMBRAI tome cream

The event will take place on Sunday July 2, in continuous service.

Please write in French, and insert the logo of the establishment of 57 and illustrate well.

THANKS

```html
<!DOCTYPE html>
<html lang="fr">
<head>
<meta charset="utf-8">
<title>Le 57 – L'andouillette de Cambrai</title>
<link href="https://fonts.googleapis.com/css2?family=Caprasimo&family=Crimson+Pro:ital,wght@1,500&family=Open+Sans:wght@700&display=swap" rel="stylesheet">
<style>
  :root {
    --olive: #9a9330;
    --wine: #8c1a2e;
    --ink: #111111;
    --desc: #6e1420;
    --venue: #5e1316;
    --cream: #fdf9ec;
    --orange: #e98a3a;
  }
  html, body { margin: 0; padding: 0; overflow: hidden; }
  .poster {
    position: relative;
    width: 1200px; height: 1200px; overflow: hidden;
    background:
      radial-gradient(ellipse 60% 60% at 58% 50%, var(--cream) 0%, #fbf2d6 45%, rgba(251,242,214,0) 78%),
      linear-gradient(135deg, #f2c66a 0%, var(--orange) 22%, #f7e3ad 50%, #f6e0a0 80%, #f3cf6a 100%);
    font-family: "Caprasimo", serif;
    text-align: center;
  }
  .line { position: absolute; left: 0; width: 1200px; margin: 0; white-space: nowrap; }
  .tower-photo {
    position: absolute; left: 956px; top: 50px; width: 244px; height: 790px;
    background: linear-gradient(180deg, rgba(180,150,120,0.12) 0%, rgba(150,105,80,0.5) 40%, rgba(140,100,75,0.4) 75%, rgba(240,220,190,0) 100%);
    border-radius: 120px 0 0 0;
  }
  .dish-photo {
    position: absolute; left: -40px; top: 330px; width: 438px; height: 745px;
    border-radius: 0 50% 50% 0;
    background: radial-gradient(ellipse at 40% 55%, #c8612a 0%, #e39a3c 42%, #f2f0ea 68%, #e9e4da 82%, rgba(240,230,210,0) 100%);
  }
  .intro { font-size: 33px; line-height: 40px; color: var(--olive); }
  .intro.l1 { top: 58px; left: -8px; }
  .intro.l2 { top: 108px; left: -8px; }
  .intro .venue { color: var(--venue); }
  .headline { color: var(--wine); font-size: 96px; line-height: 100px; }
  .headline.l1 { top: 170px; left: 20px; }
  .headline.l2 { top: 258px; left: 20px; }
  .headline .small { font-size: 62px; }
  .lead { font-size: 26px; line-height: 34px; color: var(--ink); width: 1200px; left: 21px; }
  .lead.l1 { top: 366px; }
  .lead.l2 { top: 400px; }
  .dish { position: absolute; left: 321px; width: 700px; margin: 0; }
  .dish h3 { margin: 0; font-weight: 400; font-size: 24px; line-height: 30px; color: var(--olive); white-space: nowrap; }
  .dish p {
    margin: 0; font-family: "Crimson Pro", serif; font-style: italic; font-weight: 500;
    font-size: 24px; line-height: 23.5px; color: var(--desc); white-space: nowrap;
  }
  .d1 { top: 462px; } .d2 { top: 562px; } .d3 { top: 678px; }
  .d4 { top: 795px; } .d5 { top: 911px; } .d6 { top: 955px; }
  .event { font-size: 24px; line-height: 30px; color: var(--ink); left: 15px; }
  .event.l1 { top: 1043px; }
  .event.l2 { top: 1075px; }
  .brand {
    position: absolute; left: 907px; top: 907px; width: 242px; height: 229px;
    display: flex; align-items: center; justify-content: center; gap: 10px;
  }
  .brand .dot { width: 16px; height: 16px; border-radius: 50%; background: var(--ink); }
  .brand .name { font-size: 44px; color: var(--ink); white-space: nowrap; }
  .contact {
    top: 1142px; font-family: "Open Sans", sans-serif; font-weight: 700; font-size: 22px; line-height: 30px; color: var(--ink);
  }
</style>
</head>
<body>
<div class="poster">
  <div class="tower-photo" role="img" aria-label="Photo du beffroi de Cambrai avec son horloge"></div>
  <div class="dish-photo" role="img" aria-label="Photo d'une assiette d'andouillette grillée, frites, salade et sauce moutarde"></div>

  <p class="line intro l1">À l'occasion de la grande braderie annuelle,</p>
  <p class="line intro l2">à Cambrai, <span class="venue">le 57</span> fête la spécialité cambrésienne</p>

  <h1 class="line headline l1">“ L'andouillette</h1>
  <p class="line headline l2"><span class="small">de</span> Cambrai ”</p>

  <p class="line lead l1">À cette occasion, nous élaborons</p>
  <p class="line lead l2">un menu spécial pour cette journée</p>

  <div class="dish d1"><h3>L'authentique andouillette de Cambrai</h3>
    <p>Sauce moutarde à l'ancienne, servie avec des frites<br>fraiches cuites au gras de bœuf et salade verte</p></div>
  <div class="dish d2"><h3>Salade d'andouillette de Cambrai</h3>
    <p>Laitue, tomates, oignons, andouillette<br>de CAMBRAI, Tome de Cambrai,<br>pommes cambrésiennes</p></div>
  <div class="dish d3"><h3>Gratin d’andouillette</h3>
    <p>Purée maison, andouillette de Cambrai,<br>Moutarde à l'ancienne, gratiné<br>à la tome de Cambrai</p></div>
  <div class="dish d4"><h3>Brushetta</h3>
    <p>Base crème, andouillette de Cambrai,<br>tome de Cambrai, oignons,<br>moutarde à l'ancienne</p></div>
  <div class="dish d5"><h3>Jambon grillé</h3></div>
  <div class="dish d6"><h3>Moules Frites</h3>
    <p>À la crème de tome de Cambrai</p></div>

  <p class="line event l1">La manifestation se déroulera</p>
  <p class="line event l2">le dimanche 2 juillet, en service continue</p>

  <div class="brand"><span class="dot"></span><span class="name">le 57</span></div>

  <p class="line contact">57 Rue des Tilleuls, CAMBRAI&nbsp; 03 27 00 41 96 • bonjour@maison-lumen.fr</p>
</div>
</body>
</html>
```